Need Business Card for our Real Estate Business with Sales Executive's Picture

PANTONE 484 C ( RED)

PANTONE 2766 C ( BLUE

Industry/Entity Type

Real Estate

Contact Information for Business Card

Name, Mobile, email, & picture of Person
Agency Phone, address, Web address

Requirements
Must have
• Our Logo Colours, Agent Picture,

```html
<!DOCTYPE html>
<html lang="en">
<head>
<meta charset="utf-8">
<title>Dunmore Real Estate – Business Card</title>
<link href="https://fonts.googleapis.com/css2?family=Cinzel:wght@500&family=Work+Sans:wght@400;500;600&display=swap" rel="stylesheet">
<style>
  :root {
    --navy: #0d1a45;
    --red: #8b1c24;
    --white: #ffffff;
    --stage: #3a3a3c;
    --suit: #2b3f8f;
  }
  * { box-sizing: border-box; margin: 0; padding: 0; }
  html, body { width: 1200px; height: 900px; overflow: hidden; }
  body {
    background: var(--stage);
    font-family: "Work Sans", sans-serif;
    position: relative;
  }
  .card {
    position: absolute;
    width: 700px;
    height: 400px;
    left: 250px;
    background: var(--white);
    border-radius: 22px;
    overflow: hidden;
  }
  .card--front { top: 40px; }
  .card--back { top: 460px; }

  .agent-photo {
    position: absolute;
    left: 0; bottom: 0;
    width: 330px; height: 340px;
    background: linear-gradient(160deg, #e8e4e0 0%, var(--suit) 55%, #1c2c6b 100%);
  }
  .wordmark {
    position: absolute;
    display: flex;
    align-items: center;
    gap: 10px;
    font-family: "Cinzel", serif;
    font-weight: 500;
    color: var(--navy);
    letter-spacing: 4px;
    white-space: nowrap;
  }
  .wordmark__square {
    width: 12px; height: 12px;
    background: var(--red);
  }
  .wordmark__name { font-size: 38px; }
  .card--front .wordmark { left: 370px; top: 175px; }
  .card--back .wordmark { left: 200px; top: 55px; }

  .back-band {
    position: absolute;
    inset: 0;
    width: 100%; height: 100%;
  }
  .agent-details {
    position: absolute;
    left: 30px; top: 172px;
    color: var(--white);
  }
  .agent-details__name {
    font-size: 26px;
    font-weight: 600;
    letter-spacing: 1px;
    text-transform: uppercase;
    line-height: 1.2;
  }
  .agent-details__role { font-size: 16px; margin: 4px 0 10px; }
  .agent-details__address { font-size: 16px; line-height: 1.35; font-style: normal; }

  .contact-list {
    position: absolute;
    left: 400px; top: 272px;
    list-style: none;
    color: var(--white);
    font-size: 17px;
    line-height: 1.5;
  }
  .contact-list li { display: flex; align-items: center; gap: 10px; }
  .contact-list svg { width: 13px; height: 13px; flex: none; }
</style>
</head>
<body>
  <section class="card card--front">
    <div class="agent-photo" role="img" aria-label="Portrait of the sales executive in a blue suit and striped tie"></div>
    <div class="wordmark">
      <span class="wordmark__square"></span>
      <span class="wordmark__name">Dunmore</span>
    </div>
  </section>

  <section class="card card--back">
    <svg class="back-band" viewBox="0 0 700 400" preserveAspectRatio="none" aria-hidden="true">
      <polygon points="0,150 700,250 700,400 0,400" fill="var(--navy)"/>
    </svg>

    <div class="wordmark">
      <span class="wordmark__square"></span>
      <span class="wordmark__name">Dunmore</span>
    </div>

    <div class="agent-details">
      <h1 class="agent-details__name">Daniel Ward</h1>
      <p class="agent-details__role">Managing Director</p>
      <address class="agent-details__address">Via Colle Verde,<br>118. 12030 Sanfront (CN)</address>
    </div>

    <ul class="contact-list">
      <li><svg viewBox="0 0 16 16"><path d="M4 1l3 3-2 2a9 9 0 0 0 5 5l2-2 3 3-2 3C7 15 1 9 1 3z" fill="var(--white)"/></svg>+852 2410 5718</li>
      <li><svg viewBox="0 0 16 16"><rect x="4" y="1" width="8" height="14" rx="2" fill="var(--white)"/></svg>+852 2410 5790</li>
      <li><svg viewBox="0 0 16 16"><rect x="1" y="3" width="14" height="10" fill="none" stroke="var(--white)" stroke-width="1.5"/><path d="M1 3l7 6 7-6" fill="none" stroke="var(--white)" stroke-width="1.5"/></svg>info@dunmorerealestate.com</li>
      <li><svg viewBox="0 0 16 16"><circle cx="8" cy="8" r="6.5" fill="none" stroke="var(--white)" stroke-width="1.5"/><path d="M1.5 8h13M8 1.5c3 3 3 10 0 13M8 1.5c-3 3-3 10 0 13" fill="none" stroke="var(--white)" stroke-width="1.2"/></svg>www.dunmorerealestate.com</li>
    </ul>
  </section>
</body>
</html>
```